Investment company needing business card

We are wanting a business card which looks sharp and easy on the eye. We are thinking of having a business card with the logo embossed on it, to really make it stand out. We will only have a small amount of information of the business card, person's name, position, email address and phone number

Contact Information for Business Card

Danielle Frost
Executive Assistant
+64 21 473 5162
danielf@harwickpartners.co.nz

Requirements
Must have
• Embossed logo
Should not have
• Not to be busy

```html
<!DOCTYPE html>
<html lang="en">
<head>
<meta charset="utf-8">
<title>Harwick Partners – Business Card</title>
<link rel="stylesheet" href="https://fonts.googleapis.com/css2?family=Open+Sans:wght@400;600;700&display=swap">
<style>
  :root {
    --bg: #e8e5e2;
    --card: #ffffff;
    --green: #2bb673;
    --green-light: #7fd3a6;
    --grey: #58595b;
    --grey-light: #9b9c9e;
    --text: #4a4b4d;
  }
  * { margin: 0; padding: 0; box-sizing: border-box; }
  html, body {
    width: 1200px;
    height: 997px;
    overflow: hidden;
    background: var(--bg);
    font-family: "Open Sans", Arial, sans-serif;
  }
  .sheet {
    width: 1200px;
    height: 997px;
    display: flex;
    flex-direction: column;
    align-items: center;
    justify-content: center;
    gap: 56px;
  }
  .card {
    position: relative;
    width: 700px;
    height: 400px;
    background: var(--card);
    box-shadow: 0 10px 26px rgba(0, 0, 0, 0.12);
    overflow: hidden;
  }
  .card-front .wave {
    position: absolute;
    inset: 0;
    width: 100%;
    height: 100%;
  }
  .brand-mark {
    position: absolute;
    top: 42px;
    right: 44px;
    font-weight: 700;
    font-size: 22px;
    letter-spacing: 2px;
    color: var(--green);
    text-transform: uppercase;
  }
  .contact {
    position: absolute;
    left: 62px;
    top: 128px;
    color: var(--text);
  }
  .contact-name {
    font-weight: 700;
    font-size: 20px;
    letter-spacing: 0.5px;
    color: var(--green);
    text-transform: uppercase;
    line-height: 1.2;
  }
  .contact-role {
    font-size: 16px;
    line-height: 1.4;
    margin-bottom: 14px;
  }
  .contact-line {
    display: flex;
    align-items: center;
    gap: 9px;
    font-size: 15px;
    line-height: 1.6;
  }
  .contact-line svg { width: 12px; height: 12px; fill: var(--green); flex: none; }
  .website {
    position: absolute;
    left: 198px;
    bottom: 34px;
    color: #ffffff;
    font-size: 17px;
    letter-spacing: 0.6px;
  }
  .card-back {
    display: flex;
    align-items: center;
    justify-content: center;
  }
  .brand-lockup {
    display: flex;
    align-items: center;
    gap: 16px;
  }
  .brand-square {
    width: 40px;
    height: 40px;
    background: var(--grey);
  }
  .brand-name {
    font-weight: 700;
    font-size: 34px;
    letter-spacing: 3px;
    color: var(--green);
    text-transform: uppercase;
  }
</style>
</head>
<body>
<main class="sheet">
  <section class="card card-front">
    <svg class="wave" viewBox="0 0 700 400" preserveAspectRatio="none" aria-hidden="true">
      <defs>
        <linearGradient id="band-fade" x1="0" y1="0" x2="1" y2="0">
          <stop offset="0" stop-color="#ffffff" stop-opacity="0.05"/>
          <stop offset="1" stop-color="#ffffff" stop-opacity="0.45"/>
        </linearGradient>
      </defs>
      <path d="M150 400 C230 330 320 290 430 262 C540 234 620 200 700 148 L700 400 Z" fill="var(--grey)"/>
      <path d="M160 400 C240 336 330 300 440 274 C550 248 625 214 700 168 L700 400 Z" fill="var(--green)"/>
      <path d="M260 330 C340 292 430 276 520 262 C600 248 655 222 700 196 L700 232 C640 256 570 270 480 284 C400 296 330 312 260 330 Z" fill="url(#band-fade)"/>
    </svg>

    <div class="brand-mark">Harwick Partners</div>

    <div class="contact">
      <p class="contact-name">Danielle Frost</p>
      <p class="contact-role">Executive Assistant</p>
      <p class="contact-line">
        <svg viewBox="0 0 24 24" aria-hidden="true"><path d="M6.6 10.8a15.1 15.1 0 0 0 6.6 6.6l2.2-2.2a1 1 0 0 1 1-.25 11.4 11.4 0 0 0 3.6.6 1 1 0 0 1 1 1V20a1 1 0 0 1-1 1A17 17 0 0 1 3 4a1 1 0 0 1 1-1h3.5a1 1 0 0 1 1 1c0 1.25.2 2.45.6 3.6a1 1 0 0 1-.25 1z"/></svg>
        +64 21 473 5162
      </p>
      <p class="contact-line">
        <svg viewBox="0 0 24 24" aria-hidden="true"><path d="M2 5h20v14H2z M4 7v.4l8 5 8-5V7l-8 5z"/></svg>
        danielf@harwickpartners.co.nz
      </p>
    </div>

    <p class="website">www.harwickpartners.co.nz</p>
  </section>

  <section class="card card-back">
    <div class="brand-lockup">
      <span class="brand-square"></span>
      <span class="brand-name">Harwick Partners</span>
    </div>
  </section>
</main>
</body>
</html>
```